Local massage therapist needs some new marketing material

Hi there! I am a massage therapist here in Denver, CO in Alder Bend(shopping and art district) of the city. My business is called Lumo Bodywork of Denver. My practice has an eastern influence and I do reflexology, thai massage and use Chinese herbs, etc. I know all my clients and pay close attention to details. I am also very respectful of tradition and it shows in how I work. I tend to like modern, clean, fun, Asian designs. I am wanting a new business card and brochure. I have a logo and branding for my business that I want used in the design. Currently, the sign for my building is purple and I think my logo was designed to be purple. I will attach pictures of it and can send whatever files are necessary so it can be integrated into the brochure, etc. I like the purple but open to using other colors as well. Thanks!
My website is lumobodyworkofdenver.example where info can be gathered about me and services/fees for brochure.
Updates

Just increased budget. Please see new feedback in discussion thread.

Thanks!

                                       HEY ALL,

Just wanted to let you know that I made a change to my website. It is on the Prices Page. I no longer have the frequent  flyer prices but I added discounts. Let me know if you have any questions. Thanks so much!

Target Market(s)

healthy, urban, educated, upper middle class, yogis

Industry/Entity Type

Marketing

Requirements
Must have
• logo stays purple
Should not have
• not too busy

```html
<!DOCTYPE html>
<html lang="en">
<head>
<meta charset="utf-8">
<title>Lumo Bodywork of Denver — Business Card</title>
<link rel="stylesheet" href="https://fonts.googleapis.com/css2?family=Open+Sans:ital,wght@0,400;0,600;0,700;1,400&display=swap">
<style>
  :root {
    --purple: #6a2f9a;
    --charcoal: #373735;
    --ink: #4a4a4a;
    --muted: #707070;
    --paper: #ffffff;
    --backdrop: #e9e9ee;
    --rule: #9a9a9a;
  }
  * { box-sizing: border-box; margin: 0; padding: 0; }
  html, body { width: 1200px; height: 987px; overflow: hidden; }
  body {
    background: var(--backdrop);
    font-family: "Open Sans", Arial, sans-serif;
    color: var(--ink);
    position: relative;
  }
  .card {
    position: absolute;
    width: 760px;
    height: 434px;
    background: var(--paper);
    border-radius: 36px;
    overflow: hidden;
    box-shadow: 0 6px 18px rgba(0,0,0,0.12);
  }
  .card--back { left: 400px; top: 46px; }
  .card--front { left: 40px; top: 510px; }

  /* Front */
  .name-tab {
    position: absolute; left: 36px; top: 34px;
    width: 12px; height: 52px; background: var(--purple);
  }
  .holder-name {
    position: absolute; left: 66px; top: 30px;
    font-size: 28px; font-weight: 700; color: var(--purple);
  }
  .holder-title {
    position: absolute; left: 66px; top: 68px;
    font-size: 17px; color: var(--muted);
  }
  .address {
    position: absolute; left: 66px; top: 128px;
    font-size: 18px; line-height: 24px; color: var(--ink);
  }
  .contact {
    position: absolute; left: 66px; top: 222px;
    list-style: none; font-size: 18px; line-height: 28px;
  }
  .contact li { display: flex; align-items: center; gap: 8px; white-space: nowrap; }
  .contact svg { width: 16px; height: 16px; fill: var(--purple); }
  .footer-band { position: absolute; left: 0; top: 0; width: 760px; height: 434px; }
  .website {
    position: absolute; left: 40px; top: 308px;
    font-size: 19px; color: var(--paper);
  }
  .brand {
    position: absolute; right: 56px; top: 140px;
    display: flex; align-items: center; gap: 18px;
    white-space: nowrap;
  }
  .brand-mark {
    width: 50px; height: 50px; border-radius: 50%;
    background: var(--purple); flex: none;
  }
  .brand-name {
    font-size: 74px; font-weight: 400; letter-spacing: 6px;
    color: var(--purple); line-height: 1;
  }

  /* Back */
  .appointment-heading {
    position: absolute; left: 0; right: 0; top: 44px;
    text-align: center; font-size: 20px; font-weight: 700;
    color: var(--purple); letter-spacing: 1px;
  }
  .field {
    position: absolute; left: 80px; right: 80px;
    display: flex; align-items: flex-end; gap: 10px;
    font-size: 19px; color: var(--ink);
  }
  .field--name { top: 100px; }
  .field--date { top: 150px; }
  .field .line { flex: 1; border-bottom: 1px solid var(--rule); height: 20px; }
  .field .line--short { flex: 0 0 250px; }
  .hours {
    position: absolute; left: 0; right: 0; top: 222px;
    text-align: center; font-size: 20px; line-height: 30px; color: var(--ink);
  }
  .cancel-note {
    position: absolute; left: 0; right: 0; top: 300px;
    text-align: center; font-size: 19px; font-style: italic; color: var(--muted);
  }
</style>
</head>
<body>

<section class="card card--back" aria-label="Appointment card, back">
  <h2 class="appointment-heading">YOUR APPOINTMENT</h2>
  <div class="field field--name"><span>Name :</span><span class="line"></span></div>
  <div class="field field--date">
    <span>Date :</span><span class="line"></span>
    <span>Time :</span><span class="line line--short"></span><span>am / pm</span>
  </div>
  <p class="hours">Tues - Fri 10am - 8pm Sat 10am-5pm<br>(Appointments required) No walk-ins please.</p>
  <p class="cancel-note">We appreciate a 24 hr. notice for cancellations</p>
</section>

<section class="card card--front" aria-label="Business card, front">
  <svg class="footer-band" viewBox="0 0 760 434" aria-hidden="true">
    <path d="M0 296 H380 C412 296 420 330 452 330 H760 V434 H0 Z" fill="#6a2f9a"/>
    <path d="M0 352 H760 V434 H0 Z" fill="#373735"/>
  </svg>
  <span class="name-tab"></span>
  <h1 class="holder-name">Your Name</h1>
  <p class="holder-title">Title</p>
  <p class="address">1480 E Alder Ave, Denver<br>CO 80206</p>
  <ul class="contact">
    <li>
      <svg viewBox="0 0 16 16"><path d="M8 0a8 8 0 1 0 0 16A8 8 0 0 0 8 0zm3.4 11.3c-.4.5-1.2.8-1.8.6C6.9 11 5 9.1 4.1 6.4c-.2-.6.1-1.4.6-1.8l.7-.5 1.4 2-.6.6c.4.9 1.2 1.7 2.1 2.1l.6-.6 2 1.4z"/></svg>
      303.555.0148
    </li>
    <li>
      <svg viewBox="0 0 16 16"><path d="M1 3h14v10H1z M1 3l7 5 7-5" fill="none" stroke="#6a2f9a" stroke-width="1.6"/></svg>
      info@lumobodyworkofdenver.example
    </li>
  </ul>
  <div class="brand">
    <span class="brand-mark"></span>
    <span class="brand-name">LUMO</span>
  </div>
  <p class="website">www.lumobodyworkofdenver.example</p>
</section>

</body>
</html>
```